Allied Health team of Physiotherapists & Occupational Therapists seek a business card design

We have our new logo, we now need our new business cards and stationary. Tidewell: Oedema & Family Clinic is seeking a generic card design to represent our whole team and individual cards for each therapist that incorporates our new logo to communicate our holistic approach that is calming, nuturing, supportive and welcoming.
Our Physiotherapists and Occupational Therapists assess, treat and provide education for people who are at risk of or who have lymphoedema. This is often as a result of treatment for cancer. We provide pre-operative and post-operative management and cancer rehabilitation in our Pilates studio. Our team also consists of Physiotherapists who have a strong interest in pelvic floor and continence management for both men and women.

Target Market(s)

Mainly women health conscious

Industry/Entity Type

Allied Health: Physiotherapy / Occupational Therapy

Contact Information for Business Card

Address: 14 Gallivant Ave Frankston 3199 Phone: 84316570 fax: 8431 6578 Email: info@tidewellcareservices.com.au Website: tidewellcareservices.com.au Facebook address: facebook.com/TidewellOedemaAndFamilyCareClinic. Room to write appointments. Individual cards need to have name, office email and individual email and professional details

Requirements
Must have
• Logo as per uploaded documents

```html
<!DOCTYPE html>
<html lang="en">
<head>
<meta charset="utf-8">
<title>Tidewell: Oedema &amp; Family Clinic — Business Card</title>
<link href="https://fonts.googleapis.com/css2?family=Open+Sans:wght@400;600&family=Oswald:wght@500&display=swap" rel="stylesheet">
<style>
  :root {
    --backdrop: #7a7a7a;
    --peach: #f8b286;
    --peach-deep: #f4a878;
    --paper: #ffffff;
    --ink: #2b2b2b;
    --shadow: rgba(0,0,0,0.28);
  }
  * { margin: 0; padding: 0; box-sizing: border-box; }
  html, body { width: 1200px; height: 874px; overflow: hidden; }
  body {
    background: var(--backdrop);
    font-family: "Open Sans", sans-serif;
    position: relative;
  }
  .card {
    position: absolute;
    top: 117px;
    width: 364px;
    height: 640px;
    box-shadow: 0 18px 40px var(--shadow);
  }
  .card--back { left: 190px; background: var(--peach); }
  .card--front { left: 646px; background: var(--paper); }

  .brand {
    position: absolute;
    left: 0; right: 0;
    display: flex;
    flex-direction: column;
    align-items: center;
    gap: 12px;
    text-align: center;
  }
  .card--back .brand { top: 250px; color: var(--paper); }
  .card--front .brand { top: 150px; color: var(--peach-deep); }
  .brand__dot {
    width: 18px; height: 18px;
    border-radius: 50%;
    background: currentColor;
  }
  .brand__name {
    font-family: "Open Sans", sans-serif;
    font-weight: 400;
    font-size: 19px;
    line-height: 1.35;
    letter-spacing: 0.5px;
    max-width: 220px;
  }

  .person {
    position: absolute;
    left: 44px;
    top: 400px;
  }
  .person__name {
    font-family: "Oswald", sans-serif;
    font-weight: 500;
    font-size: 24px;
    color: var(--peach-deep);
    letter-spacing: 0.5px;
    line-height: 1;
  }
  .person__title {
    font-size: 9px;
    color: var(--ink);
    margin-top: 4px;
  }

  .contact {
    position: absolute;
    left: 44px;
    top: 476px;
    list-style: none;
    display: flex;
    flex-direction: column;
    gap: 7px;
  }
  .contact__item {
    display: flex;
    align-items: center;
    gap: 10px;
    font-size: 12.5px;
    color: var(--ink);
    line-height: 1.2;
  }
  .contact__icon {
    flex: none;
    width: 20px; height: 20px;
    border-radius: 50%;
    background: var(--peach);
    display: flex; align-items: center; justify-content: center;
  }
  .contact__icon svg { width: 12px; height: 12px; }
</style>
</head>
<body>

<section class="card card--back" aria-label="Card back">
  <div class="brand">
    <span class="brand__dot"></span>
    <span class="brand__name">Tidewell: Oedema &amp; Family Clinic</span>
  </div>
</section>

<section class="card card--front" aria-label="Card front">
  <div class="brand">
    <span class="brand__dot"></span>
    <span class="brand__name">Tidewell: Oedema &amp; Family Clinic</span>
  </div>

  <div class="person">
    <p class="person__name">MAREN HOLLOWAY</p>
    <p class="person__title">CEO/Managing Director</p>
  </div>

  <ul class="contact">
    <li class="contact__item">
      <span class="contact__icon">
        <svg viewBox="0 0 12 12"><path d="M3 1.5 4.6 3.4 3.7 4.6a6 6 0 0 0 3.7 3.7l1.2-.9 1.9 1.6-.9 1.5C5.5 10.5 1.5 6.5 1.5 2.4z" fill="#fff"/></svg>
      </span>
      230-004-5716
    </li>
    <li class="contact__item">
      <span class="contact__icon">
        <svg viewBox="0 0 12 12"><path d="M6 1.5 1.5 5.5h1.3v4.8h2.4V7.5h1.6v2.8h2.4V5.5h1.3z" fill="#fff"/></svg>
      </span>
      230-004-5716
    </li>
    <li class="contact__item">
      <span class="contact__icon">
        <svg viewBox="0 0 12 12"><rect x="1.5" y="3" width="9" height="6.2" fill="none" stroke="#fff" stroke-width="1"/><path d="M1.5 3 6 6.6 10.5 3" fill="none" stroke="#fff" stroke-width="1"/></svg>
      </span>
      marenholloway@tidewellmail.net
    </li>
    <li class="contact__item">
      <span class="contact__icon"></span>
      www.harbourlanecare.com
    </li>
    <li class="contact__item">
      <span class="contact__icon">
        <svg viewBox="0 0 12 12"><path d="M6 1.2a3.4 3.4 0 0 0-3.4 3.4C2.6 7.3 6 11 6 11s3.4-3.7 3.4-6.4A3.4 3.4 0 0 0 6 1.2zm0 4.7a1.3 1.3 0 1 1 0-2.6 1.3 1.3 0 0 1 0 2.6z" fill="#fff"/></svg>
      </span>
      <span>418 Linden Row NW<br>Suite 210.Ashford Falls Mi 49620</span>
    </li>
  </ul>
</section>

</body>
</html>
```